MS Word and MS Powerpoint template creation using existing logo as style guide

Create a professional looking MS Word document template and MS powerpoint template for Torvane Advisory Pty Ltd using a logo that's already been created as the style guide. Torvane is a professional services business providing strategy, governance and execution support to small and medium business, Boards and executive teams. refer design brief.

Target Market(s)

Small to medium business, Chairs, Boards, executive teams, general managers

Industry/Entity Type

Professional business services, consultancy, business support outsourcing

Other font styles liked:
• calibri

Requirements
Must have
• leverage the existing logo for colour scheme. Use the TORVANE logo type font. Fully editable templates Word and MS Powerpoint,
Nice to have
• Refer to the design brief
Should not have
• animations, cartoons, stock images of people.

```html
<!DOCTYPE html>
<html lang="en">
<head>
<meta charset="utf-8">
<title>Torvane Advisory – Presentation Slides</title>
<link rel="stylesheet" href="https://fonts.googleapis.com/css2?family=Montserrat:wght@300;400;500;600;700&display=swap">
<style>
  :root{
    --navy:#1b2f44;
    --slate:#3b5163;
    --charcoal:#4a4d50;
    --grey:#878787;
    --grey-light:#a9a9a9;
    --ring-track:#dedede;
    --ink:#111;
    --muted:#a3a3a3;
    --paper:#fff;
    --backdrop:#d3d3cc;
  }
  *{box-sizing:border-box;margin:0;padding:0}
  html,body{width:995px;height:1200px;overflow:hidden}
  body{background:var(--backdrop);font-family:'Montserrat',sans-serif;color:var(--ink);position:relative}
  .slide{position:absolute;width:433px;height:242px;background:var(--paper);overflow:hidden}
  .slide-chart{position:absolute;left:0;top:0;width:433px;height:242px}
  .eyebrow{position:absolute;left:50px;top:30px;font-size:6px;font-weight:600;letter-spacing:2.6px}
  .rule{position:absolute;left:0;top:54px;width:30px;height:1px;background:var(--ink)}
  .slide-title{position:absolute;left:50px;top:45px;font-size:16.5px;line-height:20px;font-weight:600}
  .page-no{position:absolute;left:10px;top:117px;font-size:5px;color:#d0d0d0}
  .brand{position:absolute;left:29px;top:220px;font-size:9.5px;letter-spacing:2.2px;font-weight:400;color:var(--navy)}
  .body-copy{font-size:4.4px;line-height:8px;color:var(--muted)}
  .market-note{position:absolute;left:40px;top:193px;width:353px;text-align:center}
  .compare-note{position:absolute;left:50px;top:100px;width:122px}
  .service-list{position:absolute;left:50px;top:102px;list-style:none}
  .service{position:relative;height:37px;padding-left:23px}
  .service svg{position:absolute;left:0;top:1px;width:15px;height:15px}
  .service h3{font-size:6.3px;font-weight:600;margin-bottom:1px}
  .service p{width:90px}
  .contact{position:absolute;left:65px;top:848px;width:444px;height:242px;background:var(--paper);overflow:hidden}
  .contact-title{position:absolute;left:41px;top:38px;font-size:19.5px;font-weight:600;letter-spacing:7px;line-height:24px}
  .contact-dash{position:absolute;left:104px;top:75px;width:29px;height:1.5px;background:var(--ink)}
  .contact-bar{position:absolute;left:70px;top:113px;width:1.2px;height:40px;background:var(--ink)}
  .contact-note{position:absolute;left:41px;top:174px;width:110px;font-size:7.2px;line-height:8.5px;font-weight:500}
  .contact-panel{position:absolute;left:273px;top:0;width:171px;height:242px;background:var(--navy);color:#fff}
  .channel{position:absolute;left:27px;width:140px;height:45px}
  .channel svg{position:absolute;left:0;top:0;width:17px;height:17px}
  .channel h3{position:absolute;left:34px;top:0;font-size:7px;line-height:8.5px;font-weight:500}
  .channel p{position:absolute;left:34px;top:19px;font-size:4.4px;line-height:8px;font-weight:300;color:#c9d0d8}
</style>
</head>
<body>

<!-- Market size -->
<section class="slide" style="left:65px;top:86px">
  <p class="eyebrow">ANALYSIS</p><span class="rule"></span>
  <h2 class="slide-title" style="top:46px">Market<br>Size</h2>
  <span class="page-no">21</span>
  <svg class="slide-chart" viewBox="0 0 433 242" font-family="Montserrat, sans-serif" fill="#fff" text-anchor="middle">
    <g fill="var(--navy)">
      <circle cx="75" cy="146" r="23"/><circle cx="139" cy="137" r="33"/>
      <circle cx="222" cy="128" r="42"/><circle cx="328" cy="115" r="55"/>
    </g>
    <text x="75" y="142" font-size="4.2" font-weight="600" letter-spacing="1.2">DESIGN</text>
    <text x="75" y="153" font-size="7.5" font-weight="300">$2.2M</text>
    <text x="139" y="129" font-size="4.2" font-weight="600" letter-spacing="1.2">AFFILIATE</text>
    <text x="139" y="145" font-size="14" font-weight="300">$6 M</text>
    <text x="222" y="118" font-size="4.2" font-weight="600" letter-spacing="1.2">MARKETING</text>
    <text x="222" y="135" font-size="16" font-weight="300">$10 K</text>
    <text x="328" y="97" font-size="4.2" font-weight="600" letter-spacing="1.2">ONLINE SALES</text>
    <text x="328" y="123" font-size="21" font-weight="300">$14 M</text>
  </svg>
  <p class="body-copy market-note">Our market sizing draws on sector data, client interviews and pricing reviews to show where<br>growth is most likely across each channel this year, for boards and owners alike.</p>
  <p class="brand">TORVANE</p>
</section>

<!-- Comparison column chart -->
<section class="slide" style="left:509px;top:86px">
  <p class="eyebrow">ANALYSIS</p><span class="rule"></span>
  <h2 class="slide-title">Comparison<br>Column Chart</h2>
  <span class="page-no">22</span>
  <p class="body-copy compare-note">Survey responses grouped by age band show how each audience weighs entertainment, business and social media content when choosing an adviser for the year ahead.</p>
  <svg class="slide-chart" viewBox="0 0 433 242" font-family="Montserrat, sans-serif" text-anchor="middle">
    <text x="313" y="49" font-size="5.8" font-weight="600" fill="var(--ink)">What's going on Customers Mind</text>
    <line x1="222" y1="187.5" x2="400" y2="187.5" stroke="#e2e2e2" stroke-width="0.6"/>
    <g font-size="4.8" font-weight="600" fill="var(--ink)">
      <rect x="231" y="72" width="12" height="115" fill="var(--charcoal)"/><text x="237" y="70">43</text>
      <rect x="247" y="123" width="12" height="64" fill="var(--grey)"/><text x="253" y="121">24</text>
      <rect x="262" y="134" width="12" height="53" fill="var(--navy)"/><text x="268" y="132">20</text>
      <rect x="291" y="120" width="12" height="67" fill="var(--charcoal)"/><text x="297" y="118">25</text>
      <rect x="306" y="69" width="12" height="118" fill="var(--grey)"/><text x="312" y="67">44</text>
      <rect x="322" y="128" width="12" height="59" fill="var(--navy)"/><text x="328" y="126">22</text>
      <rect x="350" y="94" width="12" height="93" fill="var(--charcoal)"/><text x="356" y="92">35</text>
      <rect x="366" y="139" width="12" height="48" fill="var(--grey)"/><text x="372" y="137">18</text>
      <rect x="381" y="94" width="12" height="93" fill="var(--navy)"/><text x="387" y="92">35</text>
    </g>
    <g font-size="4.2" fill="var(--muted)">
      <text x="253" y="195">Under 18</text><text x="312" y="195">Between 20-40</text><text x="372" y="195">Between 40-60</text>
    </g>
    <g font-size="4" font-weight="500" fill="var(--ink)" letter-spacing="0.4">
      <text x="262" y="202">■ ENTERTAINMENT</text><text x="316" y="202">■ BUSINESS</text><text x="364" y="202">■ SOCIAL MEDIA</text>
    </g>
  </svg>
  <p class="brand">TORVANE</p>
</section>

<!-- Comparison mountain chart -->
<section class="slide" style="left:65px;top:340px">
  <p class="eyebrow">ANALYSIS</p><span class="rule"></span>
  <h2 class="slide-title">Comparison<br>Mountain Chart</h2>
  <span class="page-no">23</span>
  <svg class="slide-chart" viewBox="0 0 433 242" font-family="Montserrat, sans-serif" text-anchor="middle">
    <g opacity="0.97">
      <path d="M53 202 C73 202 75 146 93 146 C111 146 113 202 133 202 Z" fill="var(--slate)"/>
      <path d="M105 202 C125 202 127 156 145 156 C163 156 165 202 185 202 Z" fill="var(--grey)" opacity="0.95"/>
      <path d="M156 202 C176 202 178 131 196 131 C214 131 216 202 236 202 Z" fill="var(--slate)" opacity="0.95"/>
      <path d="M207 202 C227 202 229 153 247 153 C265 153 267 202 287 202 Z" fill="var(--grey)" opacity="0.95"/>
      <path d="M259 202 C279 202 281 107 299 107 C317 107 319 202 339 202 Z" fill="var(--slate)" opacity="0.95"/>
      <path d="M311 202 C331 202 333 131 351 131 C369 131 371 202 391 202 Z" fill="var(--grey)" opacity="0.95"/>
    </g>
    <line x1="53" y1="202.3" x2="391" y2="202.3" stroke="#e6e6e6" stroke-width="0.5"/>
    <g stroke="var(--ink)" stroke-width="0.8">
      <line x1="93" y1="132" x2="93" y2="140"/><line x1="145" y1="144" x2="145" y2="151"/>
      <line x1="196" y1="117" x2="196" y2="125"/><line x1="247" y1="142" x2="247" y2="149"/>
      <line x1="299" y1="94" x2="299" y2="101"/><line x1="351" y1="118" x2="351" y2="126"/>
    </g>
    <g font-size="5.6" font-weight="600" fill="var(--ink)">
      <text x="93" y="128">$14M</text><text x="145" y="140">$12M</text><text x="196" y="113">$17M</text>
      <text x="247" y="138">$13M</text><text x="299" y="90">$22M</text><text x="351" y="113">$18M</text>
    </g>
    <g font-size="4.8" font-weight="600" fill="var(--ink)">
      <text x="93" y="211">Brightfold</text><text x="145" y="211">Chatterly</text><text x="196" y="211">Linkwell</text>
      <text x="247" y="211">Viewstream</text><text x="299" y="211">Reelhaus</text><text x="351" y="211">Snapgrid</text>
    </g>
  </svg>
  <p class="brand">TORVANE</p>
</section>

<!-- Simple column chart -->
<section class="slide" style="left:509px;top:340px">
  <p class="eyebrow">ANALYSIS</p><span class="rule"></span>
  <h2 class="slide-title">Simple<br>Column Chart</h2>
  <span class="page-no">24</span>
  <svg class="slide-chart" viewBox="0 0 433 242" font-family="Montserrat, sans-serif" text-anchor="middle">
    <line x1="55" y1="202.5" x2="400" y2="202.5" stroke="#e6e6e6" stroke-width="0.5"/>
    <g fill="var(--navy)">
      <rect x="61.6" y="153" width="14" height="49"/><rect x="90.2" y="147" width="14" height="55"/>
      <rect x="118.7" y="139" width="14" height="63"/><rect x="147.9" y="131.4" width="14" height="70.6"/>
      <rect x="177" y="119.7" width="14" height="82.3"/><rect x="205.6" y="153" width="14" height="49"/>
      <rect x="234.7" y="172.6" width="14" height="29.4"/><rect x="263.3" y="166.7" width="14" height="35.3"/>
      <rect x="292.5" y="131.4" width="14" height="70.6"/><rect x="321" y="145.2" width="14" height="56.8"/>
      <rect x="350.2" y="153" width="14" height="49"/><rect x="378.8" y="172.6" width="14" height="29.4"/>
    </g>
    <g font-size="4.6" font-weight="600" fill="var(--ink)">
      <text x="68.6" y="150">25,000</text><text x="97.2" y="144">28,000</text><text x="125.7" y="136">32,000</text>
      <text x="154.9" y="128.4">36,000</text><text x="184" y="116.7">42,000</text><text x="212.6" y="150">25,000</text>
      <text x="241.7" y="169.6">15,000</text><text x="270.3" y="163.7">18,000</text><text x="299.5" y="128.4">36,000</text>
      <text x="328" y="142.2">29,000</text><text x="357.2" y="150">25,000</text><text x="385.8" y="169.6">15,000</text>
    </g>
    <g font-size="4.3" fill="var(--muted)">
      <text x="68.6" y="211">Jan</text><text x="97.2" y="211">Feb</text><text x="125.7" y="211">Mar</text>
      <text x="154.9" y="211">Apr</text><text x="184" y="211">May</text><text x="212.6" y="211">Jun</text>
      <text x="241.7" y="211">Jul</text><text x="270.3" y="211">Aug</text><text x="299.5" y="211">Sep</text>
      <text x="328" y="211">Oct</text><text x="357.2" y="211">Nov</text><text x="385.8" y="211">Dec</text>
    </g>
  </svg>
  <p class="brand">TORVANE</p>
</section>

<!-- Simple pie chart -->
<section class="slide" style="left:65px;top:594px">
  <p class="eyebrow">ANALYSIS</p><span class="rule"></span>
  <h2 class="slide-title">Simple<br>Pie Chart</h2>
  <span class="page-no">25</span>
  <ul class="service-list">
    <li class="service">
      <svg viewBox="0 0 16 16" fill="none" stroke="var(--ink)" stroke-width="0.8"><path d="M2 3 L2 8 L9 15 L15 9 L8 2 L3 2 Z"/><circle cx="5" cy="5" r="1"/></svg>
      <h3>Branding &amp; Promotions</h3>
      <p class="body-copy">Brand work that builds trust with boards and owners.</p>
    </li>
    <li class="service">
      <svg viewBox="0 0 16 16" fill="none" stroke="var(--ink)" stroke-width="0.8"><path d="M1 4 H15 M1 8 H15 M1 12 H15"/><circle cx="5" cy="4" r="1.2" fill="#fff"/><circle cx="11" cy="8" r="1.2" fill="#fff"/><circle cx="6" cy="12" r="1.2" fill="#fff"/></svg>
      <h3>Analytics</h3>
      <p class="body-copy">Clear reporting that turns data into sound decisions.</p>
    </li>
    <li class="service">
      <svg viewBox="0 0 16 16" fill="none" stroke="var(--ink)" stroke-width="0.8"><rect x="1.5" y="2.5" width="13" height="12" rx="1"/><path d="M1.5 6 H14.5 M5 1 V4 M11 1 V4"/><text x="8" y="13" font-size="6" text-anchor="middle" fill="var(--ink)" stroke="none" font-family="Montserrat, sans-serif">31</text></svg>
      <h3>SEO Services</h3>
      <p class="body-copy">Search work that keeps your firm easy to find.</p>
    </li>
  </ul>
  <svg class="slide-chart" viewBox="0 0 433 242" font-family="Montserrat, sans-serif" text-anchor="middle">
    <g stroke="#fff" stroke-width="0.6">
      <path d="M289 139 L289 78 A61 61 0 1 1 241.6 177.4 Z" fill="var(--navy)"/>
      <path d="M289 139 L241.6 177.4 A61 61 0 0 1 249.8 92.3 Z" fill="var(--grey)"/>
      <path d="M289 139 L249.8 92.3 A61 61 0 0 1 289 78 Z" fill="var(--grey-light)"/>
    </g>
    <g font-size="6.5" font-weight="600" fill="#fff">
      <text x="317" y="155">82%</text><text x="259" y="139">32%</text><text x="275" y="102">14%</text>
    </g>
    <g font-size="4" fill="var(--muted)">
      <text x="270" y="212">■ 2015</text><text x="291" y="212">■ 2016</text><text x="313" y="212">■ 2017</text>
    </g>
  </svg>
  <p class="brand">TORVANE</p>
</section>

<!-- Progress rings -->
<section class="slide" style="left:509px;top:594px">
  <p class="eyebrow">ANALYSIS</p><span class="rule"></span>
  <h2 class="slide-title">Simple<br>Column Chart</h2>
  <span class="page-no">26</span>
  <svg class="slide-chart" viewBox="0 0 433 242" font-family="Montserrat, sans-serif" text-anchor="middle">
    <g fill="none" stroke-width="2.3">
      <circle cx="80" cy="137" r="28.6" stroke="var(--ring-track)"/>
      <circle cx="80" cy="137" r="28.6" stroke="var(--navy)" stroke-dasharray="147.4 179.7" transform="rotate(-90 80 137)"/>
      <circle cx="168" cy="137" r="28.6" stroke="var(--ring-track)"/>
      <circle cx="168" cy="137" r="28.6" stroke="var(--navy)" stroke-dasharray="118.6 179.7" transform="rotate(-90 168 137)"/>
      <circle cx="264" cy="137" r="28.6" stroke="var(--ring-track)"/>
      <circle cx="264" cy="137" r="28.6" stroke="var(--navy)" stroke-dasharray="98.8 179.7" transform="rotate(-90 264 137)"/>
      <circle cx="367" cy="137" r="28.6" stroke="var(--ring-track)"/>
      <circle cx="367" cy="137" r="28.6" stroke="var(--navy)" stroke-dasharray="46.7 179.7" transform="rotate(-90 367 137)"/>
    </g>
    <g font-size="14.5" font-weight="300" fill="var(--charcoal)">
      <text x="80" y="142">82%</text><text x="168" y="142">66%</text><text x="264" y="142">55%</text><text x="367" y="142">26%</text>
    </g>
    <g stroke="var(--ink)" stroke-width="0.8">
      <line x1="80" y1="171" x2="80" y2="179"/><line x1="168" y1="171" x2="168" y2="179"/>
      <line x1="264" y1="171" x2="264" y2="179"/><line x1="367" y1="171" x2="367" y2="179"/>
    </g>
    <g font-size="6" font-weight="600" fill="var(--ink)">
      <text x="80" y="190">Texas</text><text x="168" y="190">New York</text><text x="264" y="190">Washington</text><text x="367" y="190">Nevada</text>
    </g>
    <g font-size="4.4" fill="var(--muted)">
      <text x="80" y="200">Share of clients renewing</text><text x="80" y="208">advisory terms</text>
      <text x="168" y="200">Share of clients renewing</text><text x="168" y="208">advisory terms</text>
      <text x="264" y="200">Share of clients renewing</text><text x="264" y="208">advisory terms</text>
      <text x="367" y="200">Share of clients renewing</text><text x="367" y="208">advisory terms</text>
    </g>
  </svg>
  <p class="brand">TORVANE</p>
</section>

<!-- Contact -->
<section class="contact">
  <h2 class="contact-title">CONTACT<br>US</h2>
  <span class="contact-dash"></span>
  <span class="contact-bar"></span>
  <p class="contact-note">We will be waiting for your nice comments and advices.</p>
  <div class="contact-panel">
    <div class="channel" style="top:48px">
      <svg viewBox="0 0 18 18" fill="none" stroke="#fff" stroke-width="0.8"><path d="M4 2 L7 5 L5.5 7 C6.5 9.5 8.5 11.5 11 12.5 L13 11 L16 14 L14 16 C8 16 2 10 2 4 Z"/><path d="M10 2 A6 6 0 0 1 16 8 M10 4.5 A3.5 3.5 0 0 1 13.5 8"/></svg>
      <h3>Call<br>US:</h3>
      <p>002 481 736 50<br>002 481 736 51</p>
    </div>
    <div class="channel" style="top:103px">
      <svg viewBox="0 0 18 18" fill="none" stroke="#fff" stroke-width="0.8"><rect x="1.5" y="4" width="15" height="10"/><path d="M1.5 4 L9 10 L16.5 4 M1.5 14 L7 9 M16.5 14 L11 9"/></svg>
      <h3>Email<br>US:</h3>
      <p>hello@torvane-advisory.com<br>team@torvane-advisory.com</p>
    </div>
    <div class="channel" style="top:158px">
      <svg viewBox="0 0 18 18" fill="none" stroke="#fff" stroke-width="0.8"><rect x="4.5" y="5" width="8" height="12" rx="4"/><path d="M8.5 5 V9.5 M4.5 9.5 H12.5 M8.5 5 C8.5 2.5 11 3 13 1.5"/></svg>
      <h3>Follow<br>US:</h3>
      <p>brightfold.com/torvane<br>chatterly.com/torvane</p>
    </div>
  </div>
</section>

</body>
</html>
```